Ridge Lass Crew (Flyer)

I want a flyer to advertise my service.
Details below, and logo's to use are attached.

A girls only after school program, 11-14yrs, as OSHC is no longer avail, dedicated to coaching & mentoring our girls into strong, independent young women.

The Brainchild of Rebecca Folwin, Ridge Lass Crew was created to address the growing demand for after school/school holiday supervision for kids moving from primary into high school, when OSHC ceases to exist.
With over 12 years experience mentoring and coaching young women in the corporate world, Bec decided to leave her role as a Director with Tarrant Trust, and follow her passion.
Bec, along with her sister Lorraine, who has over 10 years experience in local communities as a Youth Worker, and is also a qualified Enrolled Nurse, embarked on building a program designed to keep parents happy (by knowing their girls are safe) and dedicated to coaching and mentoring our girls into strong, independent young women.
Open every afternoon and during school holidays, we look to offer;
- Daily meditation
- Healthy snacks
- Dedicated homework time
- Organised group activity, led by qualified instructors (yoga, fitness class, soccer etc)
- Regular guests speakers, addressing issues/concerns for young people today
- SOCIAL MEDIA FREE ZONE

Located 87 Pelham Pde, Baulkham Hills (across from Crestmoor Day Clinic)
Open 3-6pm Monday to Friday

Facebook page: http://fb.example/ridgelasscrew
Email: info@ridgelasscrew.example.au
Mobile: 0455817396

Target Market(s)

Parents of teenage girls, teenage girls 11-14 years

Industry/Entity Type

School

Font styles to use
Sans Serif

Colors
b768aa
e667a6

Requirements
Must have
• What progam is - see brief
• Who runs it
Should not have
• Not be too busy, not overly mature images

```html
<!DOCTYPE html>
<html lang="en">
<head>
<meta charset="utf-8">
<title>Ridge Lass Crew – After School Program Flyer</title>
<link rel="stylesheet" href="https://fonts.googleapis.com/css2?family=Amaranth:wght@400;700&family=Cinzel:wght@400;600&family=Crimson+Text:ital,wght@1,400;1,600&family=Merriweather:wght@400&family=Open+Sans:wght@400;700&family=Rubik:wght@800&display=swap">
<style>
  :root {
    --purple: #b768aa;
    --pink: #e667a6;
    --pink-soft: #e77cb4;
    --banner-deep: #0b5fae;
    --banner-light: #3fb2ea;
    --white: #ffffff;
    --ink: #2a1630;
    --ink-grey: #3b3b3b;
    --ring: #d9d9d9;
  }
  html, body {
    margin: 0;
    padding: 0;
    overflow: hidden;
    background: var(--purple);
  }
  .flyer {
    position: relative;
    width: 927px;
    height: 1200px;
    overflow: hidden;
    background: var(--purple);
    font-family: "Open Sans", sans-serif;
    color: var(--white);
  }
  .banner {
    position: absolute;
    left: 0; top: 64px;
    width: 927px; height: 441px;
    background: linear-gradient(135deg, var(--banner-light) 0%, #1f86d4 50%, var(--banner-deep) 100%);
  }
  .banner-word {
    position: absolute;
    font-family: "Rubik", sans-serif;
    font-weight: 800;
    color: #e9f6fd;
    letter-spacing: 2px;
    margin: 0;
    line-height: 1;
  }
  .word-teamwork { left: 345px; top: 30px; font-size: 52px; }
  .word-support  { left: 485px; top: 110px; font-size: 64px; }
  .word-strategy { left: 415px; top: 235px; font-size: 64px; }
  .photo-portrait {
    position: absolute;
    left: 0; top: 160px;
    width: 160px; height: 345px;
    background: linear-gradient(160deg, #e7c6b4 0%, #c99a84 55%, #5c4a4a 100%);
  }
  .brand-tile {
    position: absolute;
    left: 50px; top: 4px;
    width: 274px; height: 330px;
    background: var(--white);
    display: flex;
    flex-direction: column;
    align-items: center;
    justify-content: center;
    gap: 14px;
  }
  .brand-dot {
    width: 22px; height: 22px;
    border-radius: 50%;
    background: var(--pink);
  }
  .brand-name {
    font-family: "Amaranth", sans-serif;
    font-weight: 700;
    font-size: 46px;
    line-height: 1.05;
    color: var(--pink);
    text-align: center;
    margin: 0;
  }
  .activity-photo {
    position: absolute;
    top: 354px;
    width: 168px; height: 168px;
    border-radius: 50%;
    border: 6px solid var(--ring);
    box-sizing: border-box;
  }
  .photo-stretch { left: 144px; background: linear-gradient(180deg, #f3efe9, #c9c3bb 60%, #2b2f45); }
  .photo-team    { left: 355px; background: linear-gradient(180deg, #6b7280, #c8303a 55%, #8a1f26); }
  .photo-beach   { left: 566px; background: linear-gradient(180deg, #9fcbe6, #d8cdb6 55%, #b9a98a); }
  .program-label {
    position: absolute;
    left: 102px; top: 540px;
    width: 732px; height: 114px;
    background: var(--pink-soft);
    border-radius: 8px;
    text-align: center;
  }
  .program-title {
    margin: 8px 0 0;
    font-family: "Amaranth", sans-serif;
    font-weight: 700;
    font-size: 33px;
    letter-spacing: 0.3px;
  }
  .program-age {
    margin: 2px 0 0;
    font-weight: 700;
    font-size: 30px;
  }
  .program-age small {
    font-size: 16px;
    font-weight: 700;
    margin-left: 4px;
  }
  .founder {
    position: absolute;
    left: 0; top: 700px;
    width: 927px;
    text-align: center;
    font-family: "Cinzel", serif;
    font-size: 26px;
    color: var(--ink);
    line-height: 40px;
    margin: 0;
    letter-spacing: 1px;
  }
  .offer-heading {
    position: absolute;
    left: 50px; top: 824px;
    margin: 0;
    font-family: "Amaranth", sans-serif;
    font-weight: 700;
    font-size: 29px;
    text-shadow: 1px 1px 2px rgba(0,0,0,0.35);
  }
  .offer-row {
    position: absolute;
    left: 0; width: 927px;
    display: flex;
    justify-content: center;
    gap: 28px;
    margin: 0; padding: 0;
    list-style: none;
    font-family: "Crimson Text", serif;
    font-style: italic;
    font-size: 23px;
  }
  .offer-row li { display: flex; align-items: center; gap: 10px; }
  .offer-row svg { width: 13px; height: 13px; flex: none; }
  .row-1 { top: 875px; }
  .row-2 { top: 920px; }
  .row-3 { top: 966px; }
  .hours-lead {
    position: absolute;
    left: 0; top: 1020px; width: 927px;
    text-align: center;
    margin: 0;
    font-family: "Merriweather", serif;
    font-size: 26px;
    color: var(--ink);
  }
  .hours-time {
    position: absolute;
    left: 310px; top: 1056px;
    margin: 0;
    font-family: "Open Sans", sans-serif;
    font-weight: 700;
    font-size: 19px;
    color: var(--ink-grey);
  }
  .contact-bar {
    position: absolute;
    left: 8px; top: 1106px;
    width: 919px; height: 94px;
    background: var(--pink-soft);
    color: var(--ink);
    font-size: 15px;
  }
  .contact-item {
    position: absolute;
    display: flex;
    gap: 10px;
    align-items: flex-start;
  }
  .contact-item p { margin: 0; line-height: 21px; }
  .icon-badge {
    width: 34px; height: 34px;
    border-radius: 50%;
    background: var(--purple);
    display: flex; align-items: center; justify-content: center;
    flex: none;
  }
  .icon-badge svg { width: 18px; height: 18px; }
  .contact-email { left: 6px; top: 4px; }
  .contact-web   { left: 14px; top: 66px; font-size: 14px; align-items: center; }
  .web-square { width: 18px; height: 18px; background: var(--purple); border-radius: 3px; flex: none; }
  .contact-phone { left: 380px; top: 12px; }
  .contact-phone strong { font-size: 17px; }
  .contact-place { left: 660px; top: 4px; }
  .contact-place small { font-size: 12px; }
</style>
</head>
<body>
<main class="flyer">

  <section class="banner">
    <p class="banner-word word-teamwork">TEAMWORK</p>
    <p class="banner-word word-support">SUPPORT</p>
    <p class="banner-word word-strategy">STRATEGY</p>
  </section>

  <div class="photo-portrait" role="img" aria-label="Photo of a smiling girl looking upward"></div>

  <div class="brand-tile">
    <span class="brand-dot"></span>
    <p class="brand-name">Ridge Lass<br>Crew</p>
  </div>

  <div class="activity-photo photo-stretch" role="img" aria-label="Photo of two girls doing a stretching exercise"></div>
  <div class="activity-photo photo-team" role="img" aria-label="Photo of a girls soccer team in red jerseys huddled with their coach"></div>
  <div class="activity-photo photo-beach" role="img" aria-label="Photo of a girl meditating on a sand dune by the sea"></div>

  <section class="program-label">
    <h1 class="program-title">A Girls Only After School Program</h1>
    <p class="program-age">11-14yrs <small>as OSHC is no longer available</small></p>
  </section>

  <p class="founder">The Brainchild of Rebecca Folwin<br>Ridge Lass Crew</p>

  <h2 class="offer-heading">We look to offer</h2>

  <ul class="offer-row row-1">
    <li><svg viewBox="0 0 14 14"><circle cx="7" cy="7" r="6" fill="none" stroke="#fff" stroke-width="1.5"/><path d="M4 7.2l2 2 4-4" fill="none" stroke="#fff" stroke-width="1.5"/></svg>Daily meditation</li>
    <li><svg viewBox="0 0 14 14"><circle cx="7" cy="7" r="6" fill="none" stroke="#fff" stroke-width="1.5"/><path d="M4 7.2l2 2 4-4" fill="none" stroke="#fff" stroke-width="1.5"/></svg>Healthy snacks</li>
    <li><svg viewBox="0 0 14 14"><circle cx="7" cy="7" r="6" fill="none" stroke="#fff" stroke-width="1.5"/><path d="M4 7.2l2 2 4-4" fill="none" stroke="#fff" stroke-width="1.5"/></svg>Dedicated homework time</li>
  </ul>
  <ul class="offer-row row-2">
    <li><svg viewBox="0 0 14 14"><circle cx="7" cy="7" r="6" fill="none" stroke="#fff" stroke-width="1.5"/><path d="M4 7.2l2 2 4-4" fill="none" stroke="#fff" stroke-width="1.5"/></svg>Organised group activity, (yoga, fitness class, soccer etc.)</li>
  </ul>
  <ul class="offer-row row-3">
    <li><svg viewBox="0 0 14 14"><circle cx="7" cy="7" r="6" fill="none" stroke="#fff" stroke-width="1.5"/><path d="M4 7.2l2 2 4-4" fill="none" stroke="#fff" stroke-width="1.5"/></svg>Regular guests speakers</li>
    <li><svg viewBox="0 0 14 14"><circle cx="7" cy="7" r="6" fill="none" stroke="#fff" stroke-width="1.5"/><path d="M4 7.2l2 2 4-4" fill="none" stroke="#fff" stroke-width="1.5"/></svg>Social media free zone</li>
  </ul>

  <p class="hours-lead">Open every afternoon and during school holidays</p>
  <p class="hours-time">3-6pm Monday to Friday</p>

  <footer class="contact-bar">
    <div class="contact-item contact-email">
      <span class="icon-badge"><svg viewBox="0 0 18 18"><rect x="1.5" y="4" width="15" height="10" rx="1" fill="none" stroke="#fff" stroke-width="1.6"/><path d="M2 5l7 5 7-5" fill="none" stroke="#fff" stroke-width="1.6"/></svg></span>
      <p>e-Mail us<br>info@ridgelasscrew.example.au</p>
    </div>
    <div class="contact-item contact-web">
      <span class="web-square"></span>
      <p>http://fb.example/ridgelasscrew</p>
    </div>
    <div class="contact-item contact-phone">
      <span class="icon-badge"><svg viewBox="0 0 18 18"><rect x="5" y="1.5" width="8" height="15" rx="1.5" fill="none" stroke="#fff" stroke-width="1.6"/><line x1="8" y1="14" x2="10" y2="14" stroke="#fff" stroke-width="1.6"/></svg></span>
      <p>Call Us Now<br><strong>0455817396</strong></p>
    </div>
    <div class="contact-item contact-place">
      <span class="icon-badge"><svg viewBox="0 0 18 18"><path d="M9 1.5a5.5 5.5 0 0 0-5.5 5.5c0 4 5.5 9.5 5.5 9.5s5.5-5.5 5.5-9.5A5.5 5.5 0 0 0 9 1.5z" fill="#fff"/><circle cx="9" cy="7" r="2" fill="#b768aa"/></svg></span>
      <p>87 Pelham Pde,<br>Baulkham Hills<br><small>(across from Crestmoor Day Clinic)</small></p>
    </div>
  </footer>

</main>
</body>
</html>
```